We need a business card design, letterhead design and envelope design for our corporate image

We are looking for a corporate business card design, letterhead and envelope design to match the business card design. Logo is done.

```html
<!DOCTYPE html>
<html lang="en">
<head>
<meta charset="utf-8">
<title>Veltrion business cards</title>
<link href="https://fonts.googleapis.com/css2?family=Montserrat:wght@400;500;600;700&display=swap" rel="stylesheet">
<style>
  :root {
    --bg: #1c1c1c;
    --card: #2a2a2a;
    --card-deep: #232323;
    --accent: #f5c400;
    --white: #ffffff;
    --silver: #8e8e8e;
    --text-soft: #e6e6e6;
  }
  * { box-sizing: border-box; margin: 0; padding: 0; }
  html, body { width: 1200px; height: 900px; overflow: hidden; }
  body {
    background: var(--bg);
    font-family: "Montserrat", sans-serif;
    position: relative;
  }
  .card {
    position: absolute;
    left: 290px;
    width: 620px;
    height: 354px;
    background: linear-gradient(135deg, var(--card) 0%, var(--card-deep) 100%);
    border-bottom: 5px solid var(--accent);
    box-shadow: 0 18px 40px rgba(0,0,0,0.55);
  }
  .card-front { top: 68px; }
  .card-back { top: 466px; }

  .brand-name {
    font-weight: 700;
    letter-spacing: -1px;
    white-space: nowrap;
  }

  .card-front .brand-name {
    position: absolute;
    left: 50%;
    top: 50%;
    transform: translate(-50%, -50%);
    font-size: 62px;
    color: var(--silver);
  }

  .card-back .brand-name {
    position: absolute;
    left: 40px;
    top: 50%;
    transform: translateY(-50%);
    font-size: 52px;
    color: var(--white);
  }

  .divider {
    position: absolute;
    left: 350px;
    top: 92px;
    width: 2px;
    height: 170px;
    background: var(--accent);
  }
  .contact {
    position: absolute;
    left: 378px;
    top: 96px;
  }
  .person-name {
    color: var(--accent);
    font-weight: 600;
    font-size: 22px;
    letter-spacing: 1.5px;
    text-transform: uppercase;
  }
  .person-role {
    color: var(--text-soft);
    font-size: 15px;
    margin-top: 2px;
    margin-bottom: 18px;
  }
  .contact-list { list-style: none; }
  .contact-list li {
    display: flex;
    align-items: center;
    gap: 8px;
    color: var(--text-soft);
    font-size: 15px;
    line-height: 24px;
  }
  .contact-list svg { width: 12px; height: 12px; flex: none; }
</style>
</head>
<body>
  <section class="card card-front">
    <span class="brand-name">Veltrion</span>
  </section>

  <section class="card card-back">
    <span class="brand-name">Veltrion</span>
    <div class="divider"></div>
    <div class="contact">
      <p class="person-name">Daniel Reyes</p>
      <p class="person-role">Director</p>
      <ul class="contact-list">
        <li>
          <svg viewBox="0 0 12 12" aria-hidden="true"><path d="M2.5 1 L4.5 1 L5.2 3.6 L4 4.6 Q5 7 7.4 8 L8.4 6.8 L11 7.5 L11 9.5 Q10.5 11 9 11 Q1 10.5 1 3 Q1 1.5 2.5 1Z" fill="var(--accent)"/></svg>
          +1 555 0142-3370
        </li>
        <li>
          <svg viewBox="0 0 12 12" aria-hidden="true"><rect x="0.8" y="2.5" width="10.4" height="7" fill="none" stroke="var(--accent)" stroke-width="1.2"/><path d="M1 3 L6 6.6 L11 3" fill="none" stroke="var(--accent)" stroke-width="1.2"/></svg>
          hello@veltrion.com
        </li>
        <li>
          <svg viewBox="0 0 12 12" aria-hidden="true"><circle cx="6" cy="6" r="5" fill="none" stroke="var(--accent)" stroke-width="1.1"/><ellipse cx="6" cy="6" rx="2.2" ry="5" fill="none" stroke="var(--accent)" stroke-width="1"/><path d="M1 6 H11" stroke="var(--accent)" stroke-width="1"/></svg>
          www.veltrion.com
        </li>
        <li>
          <svg viewBox="0 0 12 12" aria-hidden="true"><path d="M6 11.5 Q1.8 6.8 1.8 4.5 A4.2 4.2 0 0 1 10.2 4.5 Q10.2 6.8 6 11.5Z" fill="var(--accent)"/><circle cx="6" cy="4.5" r="1.5" fill="var(--card)"/></svg>
          Lakemont, NV USA
        </li>
      </ul>
    </div>
  </section>
</body>
</html>
```